OBK Farcoast Logistics Limited

We need the buissnes card to be very exclusive. As we are all young in our company. We need this to be the gate to make our clients feel deep interest for us.

We are focused in as International Trade advisors, and our products go from Oil Tanker Ships to Rubber balls for dogs.

Our Slogan is Near to Every Shore.
And our main marketing will be through Internet.

We were stablished in 2009 In Mexico and we also have offices in Hong Kong.
We have representatives in China and Europe.

Target Market(s)

Is every company or Individual that wants to develop an International Project or product development or Logistic service of Goods and people.
Some of our current projects are Ship Brokerage, Mine Brokerage, Real State and Product Pormotional development.

Industry/Entity Type

It Company

Requirements
Must have
• Our Logo and slogan, and make the card accoriding to the logo.
Nice to have
• Our Colors

```html
<!DOCTYPE html>
<html lang="en">
<head>
<meta charset="utf-8">
<title>Business Card – Front and Back</title>
<link rel="stylesheet" href="https://fonts.googleapis.com/css2?family=Open+Sans:wght@400;600;700&display=swap">
<style>
  :root {
    --backdrop: #e9e6e1;
    --card-black: #121212;
    --card-grain-light: #2e2e2e;
    --card-grain-dark: #0c0c0c;
    --brand-green: #8dc63f;
    --brand-blue: #1e88d6;
    --text-white: #f2f2f2;
    --text-muted: #cfcfcf;
    --divider: #4a4a4a;
  }
  * { box-sizing: border-box; margin: 0; padding: 0; }
  html, body {
    width: 1200px; height: 720px; overflow: hidden;
    background: var(--backdrop);
    font-family: "Open Sans", Arial, sans-serif;
  }
  .canvas {
    width: 1200px; height: 720px;
    display: flex; align-items: center; justify-content: center; gap: 40px;
  }
  .card {
    position: relative;
    width: 540px; height: 309px;
    background: var(--card-black);
    border-radius: 4px;
    overflow: hidden;
    box-shadow: 0 6px 18px rgba(0,0,0,.25);
  }

  /* Company name block */
  .brand {
    position: absolute;
    display: flex; flex-direction: column; align-items: center;
  }
  .brand__row { display: flex; align-items: center; gap: 12px; }
  .brand__dot {
    width: 14px; height: 14px; border-radius: 50%;
    background: var(--brand-blue); flex: none;
  }
  .brand__name {
    font-weight: 600; letter-spacing: 4px; line-height: 1;
    color: var(--brand-green);
  }
  .tagline {
    color: var(--text-muted); font-weight: 400; letter-spacing: .4px;
  }

  /* Front side */
  .card-front__texture {
    position: absolute; inset: 0 0 78px 0;
    background: radial-gradient(ellipse at 60% 40%, var(--card-grain-light) 0%, var(--card-grain-dark) 75%);
  }
  .card-front .brand { left: 30px; top: 86px; width: 220px; gap: 14px; }
  .card-front .brand__name { font-size: 50px; }
  .card-front .tagline { font-size: 11px; }

  .card-front__divider {
    position: absolute; left: 272px; top: 24px; height: 190px; width: 1px;
    background: linear-gradient(to bottom, transparent, var(--divider), transparent);
  }
  .contact {
    position: absolute; left: 292px; top: 32px;
    color: var(--text-white); font-size: 13px; line-height: 1.4;
  }
  .contact__name { color: var(--brand-green); font-weight: 700; font-size: 17px; }
  .contact__title { font-size: 12px; margin-bottom: 6px; color: var(--text-muted); }
  .contact__line { display: flex; align-items: center; gap: 7px; }
  .contact__line svg { width: 11px; height: 11px; fill: var(--brand-green); flex: none; }
  .contact__address { margin-top: 10px; font-size: 12.5px; }

  .card-front__band {
    position: absolute; left: 0; right: 0; bottom: 0; height: 78px;
    display: flex; flex-direction: column;
  }
  .card-front__band-rule { height: 4px; background: var(--brand-blue); flex: none; }
  .card-front__band-base {
    flex: 1; background: var(--brand-green);
    display: flex; align-items: center; justify-content: center;
    padding-left: 90px;
  }
  .web { font-size: 16px; font-weight: 600; letter-spacing: 3.5px; }
  .card-front .web { color: var(--card-black); }

  /* Back side */
  .card-back .brand { left: 0; right: 0; top: 78px; gap: 16px; }
  .card-back .brand__dot { width: 18px; height: 18px; }
  .card-back .brand__name { font-size: 72px; }
  .card-back .tagline { font-size: 14px; }
  .card-back .web {
    position: absolute; left: 0; right: 0; bottom: 48px; text-align: center;
    color: var(--text-white); font-weight: 400; font-size: 18px; letter-spacing: 5px;
  }
</style>
</head>
<body>
<main class="canvas">

  <section class="card card-front" aria-label="Business card, front">
    <div class="card-front__texture" role="img" aria-label="Dark brushed wood-grain texture"></div>

    <div class="brand">
      <div class="brand__row">
        <span class="brand__dot"></span>
        <span class="brand__name">OBK</span>
      </div>
      <span class="tagline">Near to Every Shore</span>
    </div>

    <div class="card-front__divider"></div>

    <div class="contact">
      <p class="contact__name">Your Name</p>
      <p class="contact__title">Title</p>
      <p class="contact__line">
        <svg viewBox="0 0 24 24" aria-hidden="true"><path d="M6.6 10.8a15.1 15.1 0 0 0 6.6 6.6l2.2-2.2a1 1 0 0 1 1-.25 11.4 11.4 0 0 0 3.6.57 1 1 0 0 1 1 1V20a1 1 0 0 1-1 1A17 17 0 0 1 3 4a1 1 0 0 1 1-1h3.5a1 1 0 0 1 1 1c0 1.25.2 2.45.57 3.57a1 1 0 0 1-.25 1z"/></svg>
        123-456-0789
      </p>
      <p class="contact__line">
        <svg viewBox="0 0 24 24" aria-hidden="true"><path d="M7 1h10a2 2 0 0 1 2 2v18a2 2 0 0 1-2 2H7a2 2 0 0 1-2-2V3a2 2 0 0 1 2-2zm0 3v14h10V4zm5 15.2a1.2 1.2 0 1 0 0 2.4 1.2 1.2 0 0 0 0-2.4z"/></svg>
        123-456-0789
      </p>
      <p class="contact__line">
        <svg viewBox="0 0 24 24" aria-hidden="true"><path d="M2 5h20v14H2zm2 2v.4l8 5.2 8-5.2V7zm0 2.8V17h16V9.8l-8 5.2z"/></svg>
        info@yourdomain.com
      </p>
      <p class="contact__address">Street Name, City Name<br>State Zip Code</p>
    </div>

    <div class="card-front__band">
      <div class="card-front__band-rule"></div>
      <div class="card-front__band-base">
        <span class="web">www.yourdomain.com</span>
      </div>
    </div>
  </section>

  <section class="card card-back" aria-label="Business card, back">
    <div class="brand">
      <div class="brand__row">
        <span class="brand__dot"></span>
        <span class="brand__name">OBK</span>
      </div>
      <span class="tagline">Near to Every Shore</span>
    </div>
    <p class="web">www.yourdomain.com</p>
  </section>

</main>
</body>
</html>
```